Design 4 pages for an event discovery website

This is a contest for the design of 4 pages for an events discovery website. The feature is part of the new sign-up process.

Please see the attached document for a full scope, mockups and the parent category icons.

Target Market(s)

18-35 Australian event goers

Industry/Entity Type

Events

Number of Pages Required

4 page

```html
<!DOCTYPE html>
<html lang="en">
<head>
<meta charset="UTF-8">
<title>Evendra – Signup</title>
<link rel="stylesheet" href="https://fonts.googleapis.com/css2?family=Open+Sans:wght@400;600;700&display=swap">
<style>
  :root {
    --teal: #5bbcbc;
    --teal-panel: #0a7b7a;
    --teal-button: #1fa8a6;
    --logo-teal: #13a4a4;
    --header-bg: #ffffff;
    --top-rule: #9a9a9a;
    --search-bg: #efefef;
    --search-text: #777777;
    --field-bg: #ffffff;
    --field-text: #6f6f6f;
    --white: #ffffff;
    --footer-bg: #1c1c1c;
    --footer-text: #9a9a9a;
    --social-dot: #3e3e3e;
  }
  * { box-sizing: border-box; margin: 0; padding: 0; }
  html, body { width: 1200px; height: 701px; overflow: hidden; }
  body { font-family: "Open Sans", Arial, sans-serif; position: relative; background: var(--header-bg); }

  .top-rule { position: absolute; left: 0; top: 0; width: 1200px; height: 3px; background: var(--top-rule); }

  .site-header { position: absolute; left: 0; top: 3px; width: 1200px; height: 108px; background: var(--header-bg); }
  .brand { position: absolute; left: 99px; top: 29px; font-size: 33px; font-weight: 700; color: var(--logo-teal); letter-spacing: 0.5px; line-height: 1; }
  .search { position: absolute; left: 779px; top: 29px; width: 174px; height: 33px; background: var(--search-bg); border-radius: 3px; }
  .search-label { position: absolute; left: 13px; top: 8px; font-size: 12px; color: var(--search-text); }
  .search-icon { position: absolute; right: 9px; top: 8px; }
  .nav-button { position: absolute; top: 29px; height: 33px; background: var(--teal); color: var(--white); font-size: 13px; font-weight: 600; text-align: center; line-height: 33px; border-radius: 3px; }
  .nav-signup { left: 959px; width: 68px; }
  .nav-login { left: 1033px; width: 67px; }

  .hero { position: absolute; left: 0; top: 111px; width: 1200px; height: 522px; overflow: hidden; }
  .hero-backdrop { position: absolute; inset: 0;
    background:
      radial-gradient(ellipse 500px 120px at 500px 470px, rgba(120,90,60,0.35), transparent 70%),
      radial-gradient(ellipse 400px 160px at 900px 420px, rgba(60,70,110,0.25), transparent 70%),
      linear-gradient(180deg, #1a1b1e 0%, #1e2024 45%, #2a2a2c 75%, #1f1e1f 100%); }

  .page-title { position: absolute; left: 100px; top: 50px; font-size: 34px; font-weight: 600; color: var(--white); letter-spacing: 0.5px; }

  .signup-panel { position: absolute; left: 99px; top: 122px; width: 320px; height: 354px; background: var(--teal-panel); }
  .field { position: absolute; left: 15px; width: 174px; height: 33px; background: var(--field-bg); border-radius: 2px; font-size: 12.5px; color: var(--field-text); line-height: 33px; padding-left: 13px; }
  .field-error { position: absolute; left: 213px; font-size: 12.5px; color: var(--white); line-height: 33px; }
  .submit { position: absolute; left: 15px; top: 293px; width: 98px; height: 35px; background: var(--teal-button); color: var(--white); font-size: 17px; font-weight: 700; text-align: center; line-height: 35px; border-radius: 2px; letter-spacing: 0.3px; }

  .benefits { position: absolute; left: 537px; top: 117px; list-style: none; }
  .benefits li { position: relative; height: 41px; padding-left: 18px; font-size: 14.5px; font-weight: 600; color: var(--white); line-height: 20px; }
  .benefits li svg { position: absolute; left: 0; top: 4px; }

  .site-footer { position: absolute; left: 0; top: 633px; width: 1200px; height: 68px; background: var(--footer-bg); }
  .copyright { position: absolute; left: 99px; top: 25px; font-size: 12.5px; color: var(--footer-text); }
  .copyright strong { color: var(--white); font-weight: 400; }
  .social { position: absolute; left: 970px; top: 20px; }
</style>
</head>
<body>
  <div class="top-rule"></div>

  <header class="site-header">
    <div class="brand">EVENDRA</div>
    <div class="search">
      <span class="search-label">Search</span>
      <svg class="search-icon" width="16" height="16" viewBox="0 0 16 16">
        <circle cx="6.5" cy="6.5" r="5" fill="none" stroke="#a8a8a8" stroke-width="2.2"/>
        <line x1="10.3" y1="10.3" x2="14.5" y2="14.5" stroke="#a8a8a8" stroke-width="2.6" stroke-linecap="round"/>
      </svg>
    </div>
    <div class="nav-button nav-signup">SIGNUP</div>
    <div class="nav-button nav-login">LOGIN</div>
  </header>

  <main class="hero">
    <div class="hero-backdrop" role="img" aria-label="Night-time city skyline with lit highway in the background"></div>

    <h1 class="page-title">SIGNUP</h1>

    <form class="signup-panel">
      <div class="field" style="top:22px">Username</div>
      <div class="field-error" style="top:22px">* error message</div>
      <div class="field" style="top:66px">Password</div>
      <div class="field-error" style="top:66px">* error message</div>
      <div class="field" style="top:110px">First name</div>
      <div class="field" style="top:149px;height:38px;line-height:43px">Date of Birth</div>
      <div class="field" style="top:198px">E-mail Address</div>
      <div class="field" style="top:244px">Confirm Password</div>
      <div class="submit">SIGNUP</div>
    </form>

    <ul class="benefits">
      <li><svg width="11" height="11" viewBox="0 0 12 12"><circle cx="6" cy="6" r="6" fill="#fff"/><path d="M4.6 3.3 7.3 6 4.6 8.7" fill="none" stroke="#1c1d20" stroke-width="1.8"/></svg>Get personalised event recommendations</li>
      <li><svg width="11" height="11" viewBox="0 0 12 12"><circle cx="6" cy="6" r="6" fill="#fff"/><path d="M4.6 3.3 7.3 6 4.6 8.7" fill="none" stroke="#1c1d20" stroke-width="1.8"/></svg>Get notified about your favourite events - never miss out again</li>
      <li><svg width="11" height="11" viewBox="0 0 12 12"><circle cx="6" cy="6" r="6" fill="#fff"/><path d="M4.6 3.3 7.3 6 4.6 8.7" fill="none" stroke="#1c1d20" stroke-width="1.8"/></svg>Follow all your favourite artists, musicians, teams and players in one place</li>
      <li><svg width="11" height="11" viewBox="0 0 12 12"><circle cx="6" cy="6" r="6" fill="#fff"/><path d="M4.6 3.3 7.3 6 4.6 8.7" fill="none" stroke="#1c1d20" stroke-width="1.8"/></svg>Follow your favourite local venues to know everything happening there</li>
      <li><svg width="11" height="11" viewBox="0 0 12 12"><circle cx="6" cy="6" r="6" fill="#fff"/><path d="M4.6 3.3 7.3 6 4.6 8.7" fill="none" stroke="#1c1d20" stroke-width="1.8"/></svg>Get curated news and feature content on your favourite artists (coming soon)</li>
      <li><svg width="11" height="11" viewBox="0 0 12 12"><circle cx="6" cy="6" r="6" fill="#fff"/><path d="M4.6 3.3 7.3 6 4.6 8.7" fill="none" stroke="#1c1d20" stroke-width="1.8"/></svg>Invite your mates to events via Socialo (SO sign-up only)</li>
    </ul>
  </main>

  <footer class="site-footer">
    <p class="copyright">Copyright &nbsp;©&nbsp; 2015 &nbsp;<strong>Evendra</strong>.&nbsp; All rights reserved</p>
    <svg class="social" width="132" height="28" viewBox="0 0 132 28" aria-label="Social links">
      <circle cx="14" cy="14" r="13.5" fill="var(--social-dot)"/>
      <circle cx="48" cy="14" r="13.5" fill="var(--social-dot)"/>
      <circle cx="82" cy="14" r="13.5" fill="var(--social-dot)"/>
      <circle cx="117" cy="14" r="13.5" fill="var(--social-dot)"/>
    </svg>
  </footer>
</body>
</html>
```